Looking for a modern, Professional business card design

We have a simple business card, but are looking for a more modern, professional look. A sample of the basic card is attached as well as the logo. We would also like to add that we offer:
Struggling with your finances?
- Learn to become debt free
- Discover the power of cash
- Control your money instead of it controlling you
Let us help you achieve a new level of financial freedom!
Also, we would like to have a "SPECIAL OFFER!: FREE 30 minute consultation"
Financial Planning

```html
<!DOCTYPE html>
<html lang="en">
<head>
<meta charset="utf-8">
<title>Horizon Money Coaching – Business Card</title>
<link href="https://fonts.googleapis.com/css2?family=Arimo:wght@400;700&display=swap" rel="stylesheet">
<style>
  :root {
    --page: #d9d6d2;
    --card: #eceeec;
    --ink: #1d1d1d;
    --muted: #5a5a5a;
    --green: #2e7d1e;
    --green-deep: #1f5c12;
    --green-light: #5fae3a;
    --stripe-dark: #2a2a2a;
  }
  * { box-sizing: border-box; margin: 0; padding: 0; }
  html, body {
    width: 1200px; height: 969px; overflow: hidden;
    background: var(--page);
    font-family: "Arimo", Arial, sans-serif;
  }
  .card {
    position: absolute; left: 100px; top: 202px;
    width: 1000px; height: 564px;
    background: var(--card);
    border-radius: 34px;
    overflow: hidden;
    box-shadow: 0 10px 30px rgba(0,0,0,0.18);
  }
  .side-stripe { position: absolute; left: 0; top: 0; width: 28px; height: 100%; display: flex; flex-direction: column; }
  .side-stripe .dark { height: 190px; background: var(--stripe-dark); }
  .side-stripe .mid { height: 190px; background: linear-gradient(var(--green-deep), var(--green)); }
  .side-stripe .low { height: 150px; background: linear-gradient(var(--green), var(--green-light)); }
  .side-stripe .end { flex: 1; background: var(--card); }

  .content { position: absolute; right: 55px; top: 0; text-align: right; }
  .brand { position: absolute; right: 0; top: 118px; display: flex; align-items: center; gap: 14px; white-space: nowrap; }
  .brand-dot { width: 36px; height: 36px; border-radius: 50%; background: var(--green); }
  .brand-name { font-weight: 700; font-size: 36px; line-height: 40px; color: var(--green-deep); letter-spacing: 0.5px; }
  .tagline { position: absolute; right: 0; top: 168px; font-size: 15px; line-height: 18px; color: var(--muted); white-space: nowrap; }

  .person-name { position: absolute; right: 0; top: 218px; font-size: 31px; line-height: 36px; font-weight: 400; color: var(--green); white-space: nowrap; }
  .person-title { position: absolute; right: 0; top: 260px; font-size: 25px; line-height: 30px; color: var(--ink); white-space: nowrap; }

  .contact { position: absolute; right: 0; top: 304px; list-style: none; }
  .contact li { display: flex; justify-content: flex-end; align-items: center; gap: 16px; height: 38px; font-size: 25px; color: var(--ink); white-space: nowrap; }
  .contact svg { width: 26px; height: 26px; }

  .pitch { position: absolute; right: 0; top: 432px; white-space: nowrap; }
  .pitch-title { font-weight: 700; font-size: 24px; line-height: 28px; color: var(--green); }
  .pitch-line { font-size: 22px; line-height: 28px; color: var(--muted); margin-top: 3px; }
  .pitch-line .sep { color: var(--green); margin: 0 6px; }

  .offer-badge { position: absolute; left: 76px; top: 372px; width: 136px; height: 136px; }
</style>
</head>
<body>
  <div class="card">
    <div class="side-stripe">
      <div class="dark"></div><div class="mid"></div><div class="low"></div><div class="end"></div>
    </div>

    <svg class="offer-badge" viewBox="0 0 150 150" aria-label="Special offer: free 30 minute consultation">
      <defs>
        <path id="badge-ring" d="M75,75 m-58,0 a58,58 0 1,1 116,0 a58,58 0 1,1 -116,0"/>
        <radialGradient id="badge-fill" cx="40%" cy="35%" r="70%">
          <stop offset="0" stop-color="#8fd05a"/>
          <stop offset="1" stop-color="#2e7d1e"/>
        </radialGradient>
      </defs>
      <circle cx="75" cy="75" r="42" fill="url(#badge-fill)" stroke="#e6e6e6" stroke-width="3"/>
      <text font-family="Arimo, Arial, sans-serif" font-weight="700" font-size="18" fill="#2a2a2a">
        <textPath href="#badge-ring" textLength="352" lengthAdjust="spacing">FREE 30 MINUTE CONSULTATION</textPath>
      </text>
      <text x="75" y="72" text-anchor="middle" font-family="Arimo, Arial, sans-serif" font-weight="700" font-size="14" fill="#1d1d1d">SPECIAL</text>
      <text x="75" y="90" text-anchor="middle" font-family="Arimo, Arial, sans-serif" font-weight="700" font-size="14" fill="#1d1d1d">OFFER!</text>
    </svg>

    <div class="content">
      <div class="brand">
        <span class="brand-dot"></span>
        <span class="brand-name">HORIZON MONEY COACHING</span>
      </div>
      <p class="tagline">Clear steps toward lasting money calm</p>

      <h1 class="person-name">Daniel R. Whitfield</h1>
      <p class="person-title">Personal Financial Coach</p>

      <ul class="contact">
        <li>(555) 014-2387
          <svg viewBox="0 0 26 26"><rect x="7" y="2" width="12" height="22" rx="2" fill="none" stroke="#2e7d1e" stroke-width="2.5"/><rect x="11" y="19" width="4" height="2" fill="#2e7d1e"/></svg>
        </li>
        <li>daniel@clearpathmoney.com
          <svg viewBox="0 0 26 26"><rect x="2" y="6" width="22" height="15" rx="1.5" fill="#2e7d1e"/><path d="M3 7 L13 15 L23 7" fill="none" stroke="#eceeec" stroke-width="2"/></svg>
        </li>
        <li>www.clearpathmoney.com
          <svg viewBox="0 0 26 26"><circle cx="13" cy="13" r="11" fill="#2e7d1e"/><ellipse cx="13" cy="13" rx="5" ry="11" fill="none" stroke="#eceeec" stroke-width="1.6"/><path d="M2 13 H24" stroke="#eceeec" stroke-width="1.6"/></svg>
        </li>
      </ul>

      <div class="pitch">
        <p class="pitch-title">STRUGGLING WITH YOUR FINANCES?</p>
        <p class="pitch-line">Learn to become debt free<span class="sep">●</span>Discover the power of cash</p>
        <p class="pitch-line">Control your money instead of it controlling you</p>
      </div>
    </div>
  </div>
</body>
</html>
```